Keystone Trench Co Business Card*

Looking for a professional, clean and crisp business card

I am in the underground utilities industry and am just looking for a really impressive business card. I would like our card to be white with our symbol crisp and clear with it protruding. I also have a business partner that will require his name and info on the card once the design is set. I would like to have our website info on the card which is;
http://keystonetrenchco.example/

Contact Information for Business Card

Website, contact name, number and email

```html
<!DOCTYPE html>
<html lang="en">
<head>
<meta charset="utf-8">
<title>Keystone Trench Co — Business Card</title>
<link rel="stylesheet" href="https://fonts.googleapis.com/css2?family=Saira+Condensed:wght@700&family=Montserrat:wght@400&display=swap">
<style>
  :root {
    --backdrop: #2a2a2a;
    --card-dark: #0b0c0e;
    --card-dark-soft: #1a1d22;
    --card-white: #ffffff;
    --accent-blue: #3f64b8;
    --ink-dark: #0b0c0e;
    --ink-light: #ffffff;
  }
  * { box-sizing: border-box; margin: 0; padding: 0; }
  html, body {
    width: 1200px; height: 900px; overflow: hidden;
    background: var(--backdrop);
  }
  .canvas {
    position: relative; width: 1200px; height: 900px;
  }
  .card {
    position: absolute; left: 250px; width: 700px; height: 400px;
    overflow: hidden;
    box-shadow: 0 10px 30px rgba(0,0,0,0.45);
  }
  .card-back { top: 30px; background: var(--card-dark); }
  .card-front { top: 470px; background: var(--card-white); }

  .back-texture {
    position: absolute; inset: 0;
    background: linear-gradient(135deg, var(--card-dark-soft) 0%, var(--card-dark) 55%, var(--card-dark-soft) 100%);
  }
  .brand {
    position: absolute; display: flex; align-items: center; gap: 12px;
    font-family: "Saira Condensed", sans-serif; font-weight: 700;
    text-transform: uppercase; letter-spacing: 1px; white-space: nowrap;
  }
  .brand-dot {
    width: 26px; height: 26px; border-radius: 50%;
    background: var(--accent-blue); flex: none;
  }
  .card-back .brand {
    right: 40px; bottom: 60px; font-size: 30px; color: var(--ink-light);
  }
  .card-front .brand {
    left: 0; right: 0; top: 80px; justify-content: center;
    font-size: 44px; color: var(--ink-dark);
  }
  .front-rule {
    position: absolute; left: 40px; right: 40px; top: 212px;
    height: 2px; background: var(--accent-blue);
  }
  .contact-band {
    position: absolute; left: 0; right: 0; bottom: 0; height: 165px;
    background: var(--card-dark);
    display: flex; align-items: center; padding: 0 40px;
  }
  .person-name {
    font-family: "Saira Condensed", sans-serif; font-weight: 700;
    font-size: 42px; letter-spacing: 2px; text-transform: uppercase;
    color: var(--ink-light); white-space: nowrap;
  }
  .band-divider {
    width: 2px; height: 84px; background: var(--accent-blue);
    margin: 0 22px 0 26px; flex: none;
  }
  .contact-list { list-style: none; }
  .contact-item {
    display: flex; align-items: center; gap: 10px;
    font-family: "Montserrat", sans-serif; font-size: 16px;
    color: var(--ink-light); line-height: 26px; white-space: nowrap;
  }
  .contact-icon { width: 16px; height: 16px; flex: none; }
  .domain-accent { color: var(--accent-blue); }
</style>
</head>
<body>
<main class="canvas">
  <section class="card card-back">
    <div class="back-texture" role="img" aria-label="Dark diagonal pattern of pipe sections"></div>
    <div class="brand"><span class="brand-dot"></span>Keystone Trench Co</div>
  </section>

  <section class="card card-front">
    <div class="brand"><span class="brand-dot"></span>Keystone Trench Co</div>
    <div class="front-rule"></div>
    <div class="contact-band">
      <h1 class="person-name">Dale Marwick</h1>
      <div class="band-divider"></div>
      <ul class="contact-list">
        <li class="contact-item">
          <svg class="contact-icon" viewBox="0 0 16 16" fill="none" stroke="#3f64b8" stroke-width="1.5"><path d="M3 2h3l1 3-2 1a8 8 0 0 0 5 5l1-2 3 1v3a1 1 0 0 1-1 1A12 12 0 0 1 2 3a1 1 0 0 1 1-1z"/></svg>
          604-555-0182
        </li>
        <li class="contact-item">
          <svg class="contact-icon" viewBox="0 0 16 16" fill="none" stroke="#3f64b8" stroke-width="1.5"><rect x="1" y="3" width="14" height="10"/><path d="M1 3l7 6 7-6"/></svg>
          Dale@keystonetrenchco.example
        </li>
        <li class="contact-item">
          <svg class="contact-icon" viewBox="0 0 16 16" fill="none" stroke="#3f64b8" stroke-width="1.5"><circle cx="8" cy="8" r="7"/><ellipse cx="8" cy="8" rx="3" ry="7"/><path d="M1 8h14"/></svg>
          <span>www.<span class="domain-accent">keystonetrenchco</span>.example</span>
        </li>
      </ul>
    </div>
  </section>
</main>
</body>
</html>
```